Website Redesign for Non-Profit Ministry & Church

NOTE: Please do not contact me privately — all private inquiries will be ignored.

Individuals seeking spiritual healing, community connection, ministry support and journal-based encounters.

Description of What’s Needed

We need a clean, fresh, inviting website that encourages engagement and connection. The site should feel warm and accessible, draw people in, and clearly present who we are, what we offer, and how visitors can participate. The layout should be straightforward, with well-structured pages (no overlapping objects, minimal layering complexity) and easy to navigate. Use only Google Fonts. All stock photos must be sourced from royalty-free sites and include proper attribution. We will not include a search feature.

Pages to Create
1. Home Page – impactful hero area, clear call-to-action, visual story of ministry, giving/gathering invitation.
2. About Us – vision, mission, leadership, testimonies, history.
3. Meetings & Events – upcoming gatherings, schedule, how to attend, sign-up or interest form.
4. Encounter: “Lanterns by the River” (book) – dedicated page for the book, overview, purchase link or details, journal prompts, imagery.
5. Healing Rooms / Ministry – explain ministry offerings, invite participation, testimonials or case-studies.
6. Live Stream & Links Page – page listing links for YouTube live stream, other platforms, archive links; simple layout.

Colour & Branding

Use colours that blend with our existing logo (attached). The palette should feel contemporary, welcoming, and aligned with ministry themes of restoration, healing and love. Ensure text, button and link colours maintain good contrast for accessibility.

Existing Content & Reference

Please gather available content from our current website in the attachment here for text, images and structure for reuse.

Imagery Guidelines

– Use original photos from our Facebook page or Google Location listing for building or people images when available.
– If generic images are used, ensure they depict appropriate ministry-related buildings or people (community, warm gathering) — avoid generic unrelated stock imagery.
– All photos must be royalty-free or have proper licensing and attribution.
– No overlapping objects or visual clutter; clean layouts with defined sections.

Additional Notes

– Integration: We currently utilise MailChimp for email communication; the design should include a connection/invite to subscribe (via MailChimp) but no blog page is required at this time.
– Payment/Giving: We accept PayPal and already have a giving portal; include clear donation/give buttons or calls-to-action linking to existing giving systems.
– No search function to be included.
– Layouts should avoid complex layering or overlapping elements—designers should work with distinct content blocks, clear visual hierarchy, and straightforward mobile-friendly structure.

Target Market(s)

Industry/Entity Type

Church/Religious institution

Number of Pages Required

5+ page

Requirements
Should not have
• search bar

```html
<!DOCTYPE html>
<html lang="en">
<head>
<meta charset="utf-8">
<title>Restored Together — Home</title>
<link href="https://fonts.googleapis.com/css2?family=Baloo+2:wght@600;700;800&family=Ubuntu:wght@400;500&family=Roboto:wght@400;700&display=swap" rel="stylesheet">
<style>
:root{
  --teal:#10a89a;
  --teal-dark:#0b8f83;
  --purple:#6a3393;
  --lavender:#efe9f3;
  --ink:#1d1d1d;
  --muted:#555;
  --white:#fff;
  --black:#000;
  --heading:"Baloo 2",sans-serif;
  --body:"Ubuntu",sans-serif;
}
*{box-sizing:border-box;margin:0;padding:0}
html,body{width:1200px;height:3349px;overflow:hidden}
body{position:relative;background:var(--white);font-family:var(--body);color:var(--ink)}
.abs{position:absolute}

/* header */
.site-header{left:0;top:0;width:1200px;height:94px;background:var(--white);z-index:5}
.brand{display:flex;align-items:center;gap:10px;font-family:var(--body);font-weight:500;color:var(--teal);font-size:22px;line-height:1.05}
.brand-dot{width:44px;height:44px;border-radius:50%;background:var(--teal);flex:none}
.site-header .brand{left:113px;top:22px}
.contact-bar{right:114px;top:12px;display:flex;gap:28px;font-size:16px;align-items:center}
.contact-bar span{display:flex;align-items:center;gap:10px}
.contact-bar .sep{width:1px;height:20px;background:#ddd}
.header-rule{left:334px;top:43px;width:866px;height:1px;background:#e6e6e6}
.main-nav{left:334px;top:55px;display:flex;gap:21px;font-size:17px}
.main-nav a{color:var(--ink);text-decoration:none}
.main-nav a.active{color:var(--teal)}
.cart{left:1070px;top:58px}

/* hero */
.hero{left:0;top:94px;width:1200px;height:640px;overflow:hidden}
.hero-photo{width:100%;height:100%;background:linear-gradient(180deg,#d8d2c6 0%,#b9a58a 45%,#3d2f7a 75%,#2c2565 100%)}
.hero-curve{left:0;bottom:0;width:1200px;height:230px}
.hero-panel{left:81px;top:140px;width:592px;height:254px;background:rgba(16,168,154,.92);border-radius:18px;padding:18px 28px;color:var(--white)}
.hero-title{font-family:var(--heading);font-size:58px;line-height:1.1;font-weight:800}
.hero-title .light{font-weight:600}
.hero-text{font-size:17px;line-height:1.55;margin-top:14px;width:420px}
.btn{display:inline-flex;align-items:center;gap:14px;height:46px;padding:0 26px 0 6px;border-radius:23px;background:var(--purple);color:var(--white);font-family:var(--body);font-weight:500;font-size:19px;text-decoration:none}
.btn-icon{width:36px;height:36px;border-radius:50%;background:var(--white)}
.hero-panel .btn{margin-top:20px}
.slider-dots{left:1130px;top:202px;display:flex;flex-direction:column;gap:10px;align-items:center}
.slider-dots i{display:block;width:11px;height:11px;border-radius:50%;background:var(--white)}
.slider-dots i.on{width:24px;height:24px;background:var(--purple);border:3px solid var(--white)}

/* about */
.about-photo{left:118px;top:823px;width:460px;height:460px;border-radius:50%;border:10px solid var(--teal);background:linear-gradient(160deg,#3aa7c9 0%,#5b4f68 45%,#c89aa8 75%,#8a7464 100%)}
.eyebrow{font-family:var(--body);font-size:26px;font-weight:400;letter-spacing:.5px}
.section-title{font-family:var(--heading);font-weight:800;color:var(--teal);font-size:48px;line-height:1}
.about-copy{left:624px;top:870px;width:470px}
.about-copy .eyebrow{margin-left:5px}
.about-copy .section-title{margin-top:10px}
.about-copy p{font-size:17px;line-height:1.3;margin-top:22px;color:#222}
.about-copy p+p{margin-top:20px}
.about-copy .btn{margin-top:38px;margin-left:-7px}

/* events */
.events{left:0;top:1394px;width:1200px;height:481px;background:var(--lavender);text-align:center}
.events .eyebrow{margin-top:57px}
.events .section-title{margin-top:8px}
.events .lead{font-size:20px;font-weight:500;line-height:1.5;width:980px;margin:30px auto 0}
.events .body{font-size:19px;line-height:1.6;width:980px;margin:18px auto 0;color:#333}
.events .btn{margin-top:30px}

/* blog */
.blog-head{left:0;top:1975px;width:1200px;text-align:center}
.blog-head .section-title{margin-top:10px}
.post-card{top:2107px;width:315px;height:402px;border:1px solid #e2e2e2;border-radius:18px;padding:10px;background:var(--white)}
.post-img{height:225px;border-radius:16px}
.post-meta{display:flex;gap:30px;font-family:"Roboto",sans-serif;font-size:13px;margin:18px 6px 0 16px}
.post-title{font-family:"Roboto",sans-serif;font-weight:700;font-size:15px;line-height:1.4;margin:14px 16px 0;text-transform:uppercase}
.post-excerpt{font-family:"Roboto",sans-serif;font-size:14px;line-height:1.5;color:var(--muted);margin:10px 16px 0}

/* footer */
.footer-shape{left:0;top:2860px;width:1200px;height:489px}
.newsletter{left:117px;top:2604px;width:967px;height:285px;background:var(--purple);border-radius:10px;text-align:center;color:var(--white);z-index:2}
.newsletter h2{font-family:var(--heading);font-size:46px;font-weight:800;margin-top:22px;line-height:1.1}
.newsletter p{font-size:18px;margin-top:10px}
.email-field{width:522px;height:43px;border-radius:22px;background:var(--white);margin:22px auto 0;text-align:left;padding:13px 16px;color:#333;font-size:15px}
.newsletter .btn{margin-top:25px;background:var(--teal)}
.footer-brand{left:0;top:2950px;width:1200px;display:flex;justify-content:center}
.footer-brand .brand{font-size:46px;gap:18px;line-height:1}
.footer-brand .brand-dot{width:110px;height:110px}
.footer-nav{left:0;top:3120px;width:1200px;display:flex;justify-content:center;gap:22px;font-size:18px;font-weight:500}
.footer-nav a{color:var(--white);text-decoration:none}
.socials{left:0;top:3184px;width:1200px;display:flex;justify-content:center;gap:8px}
.socials a{width:43px;height:43px;border:2px solid var(--white);border-radius:50%;background:#000;display:flex;align-items:center;justify-content:center}
.copyright{left:0;top:3272px;width:1200px;text-align:center;color:var(--white);font-size:15px}
</style>
</head>
<body>

<header class="site-header abs">
  <div class="brand abs"><span class="brand-dot"></span><span>Restored<br>Together</span></div>
  <div class="contact-bar abs">
    <span><svg width="16" height="12" viewBox="0 0 16 12"><rect width="16" height="12" rx="1" fill="#10a89a"/><path d="M0 1l8 6 8-6" stroke="#fff" stroke-width="1.5" fill="none"/></svg>hello@restoredtogether.org</span>
    <span class="sep"></span>
    <span><svg width="14" height="14" viewBox="0 0 24 24"><path fill="#10a89a" d="M6.6 10.8a15 15 0 006.6 6.6l2.2-2.2a1 1 0 011-.25 11.4 11.4 0 003.6.57 1 1 0 011 1V20a1 1 0 01-1 1A17 17 0 013 4a1 1 0 011-1h3.5a1 1 0 011 1c0 1.250.2 2.450.57 3.6a1 1 0 01-.25 1z"/></svg>+1 555-010-4827</span>
  </div>
  <div class="header-rule abs"></div>
  <nav class="main-nav abs">
    <a class="active" href="#">Home</a><a href="#">About Us</a><a href="#">Meetings &amp; Events</a><a href="#">Encounter</a><a href="#">Healing Rooms</a><a href="#">Live Stream</a>
  </nav>
  <svg class="cart abs" width="18" height="16" viewBox="0 0 18 16"><path d="M0 1h3l2.5 9h10l2-7H5" stroke="#10a89a" stroke-width="2" fill="#10a89a"/><circle cx="7" cy="14" r="1.6" fill="#10a89a"/><circle cx="14" cy="14" r="1.6" fill="#10a89a"/></svg>
</header>

<section class="hero abs">
  <div class="hero-photo" role="img" aria-label="Speaker with a microphone addressing a seated congregation in a church hall"></div>
  <svg class="hero-curve abs" viewBox="0 0 1200 230" preserveAspectRatio="none">
    <path d="M0 100 Q600 330 1200 60 L1200 230 L0 230 Z" fill="#10a89a"/>
    <path d="M0 130 Q600 320 1200 90 L1200 230 L0 230 Z" fill="#fff"/>
  </svg>
  <div class="hero-panel abs">
    <h1 class="hero-title">Restored <span class="light">Together</span></h1>
    <p class="hero-text">We are a church that believes in Jesus, a church that loves God and people!</p>
    <a class="btn" href="#"><span class="btn-icon"></span>Get Started</a>
  </div>
  <div class="slider-dots abs"><i class="on"></i><i></i><i></i><i></i></div>
</section>

<section>
  <div class="about-photo abs" role="img" aria-label="Three smiling women from the congregation standing together"></div>
  <div class="about-copy abs">
    <h3 class="eyebrow">ABOUT US</h3>
    <h2 class="section-title">Our Mission &amp; Vision</h2>
    <p>Honoring God’s presence by loving the broken, saving the lost, and healing the hurting through the demonstration of His love and power.</p>
    <p>Restored Together is here to activate, proclaim and teach the love of the Father through Jesus with the guidance of the Holy Spirit.</p>
    <a class="btn" href="#"><span class="btn-icon"></span>Read More</a>
  </div>
</section>

<section class="events abs">
  <h3 class="eyebrow">MEETINGS &amp; EVENTS</h3>
  <h2 class="section-title">Upcoming Gatherings</h2>
  <p class="lead">If you are hosting an event at your church or ministry, as you prayerfully seek the Lord for guidance review these thoughts regarding Elaine &amp; Thomas Harwick and their ministry.</p>
  <p class="body">I have served in church leadership with Elaine and Thomas for several years, and I do not know of a more balanced and powerful ministry of miracles and healings. They are activators not only of supernatural demonstrations but of supernatural compassion.</p>
  <a class="btn" href="#"><span class="btn-icon"></span>Schedule</a>
</section>

<section>
  <div class="blog-head abs">
    <h3 class="eyebrow">RECENT POSTS</h3>
    <h2 class="section-title">Upcoming Blog</h2>
  </div>
  <article class="post-card abs" style="left:113px">
    <div class="post-img" role="img" aria-label="Wooden cross silhouetted against a purple and gold sunset sky" style="background:linear-gradient(180deg,#4a5fa0 0%,#c07ab0 50%,#f2b36a 80%,#3a2c3e 100%)"></div>
    <div class="post-meta"><span>▦ 22/11/25</span><span>◷ 15 MINS</span></div>
    <h4 class="post-title">Nothing is incurable for God</h4>
    <p class="post-excerpt">Lorem ipsum dolor sit amet, consectetur adipiscing elit, sed do eiusmod tempor</p>
  </article>
  <article class="post-card abs" style="left:443px">
    <div class="post-img" role="img" aria-label="Rainbow arching over a long open road" style="background:linear-gradient(180deg,#8d9aa6 0%,#b4b9b2 50%,#7d8a5e 70%,#55575a 100%)"></div>
    <div class="post-meta"><span>▦ 22/11/25</span><span>◷ 15 MINS</span></div>
    <h4 class="post-title">Healing amidst the car accident</h4>
    <p class="post-excerpt">Lorem ipsum dolor sit amet, consectetur adipiscing elit, sed do eiusmod tempor</p>
  </article>
  <article class="post-card abs" style="left:772px">
    <div class="post-img" role="img" aria-label="Bird soaring over trees at a golden sunrise" style="background:linear-gradient(180deg,#e08a1e 0%,#f6c446 50%,#d77d18 80%,#4a2a0c 100%)"></div>
    <div class="post-meta"><span>▦ 22/11/25</span><span>◷ 15 MINS</span></div>
    <h4 class="post-title">Healing – where and how can it happen?</h4>
    <p class="post-excerpt">Lorem ipsum dolor sit amet, consectetur adipiscing elit, sed do eiusmod tempor</p>
  </article>
</section>

<footer>
  <svg class="footer-shape abs" viewBox="0 0 1200 489" preserveAspectRatio="none">
    <path d="M0 80 Q600 -60 1200 80 L1200 489 L0 489 Z" fill="#000"/>
    <path d="M1000 0 Q1120 30 1200 70 L1200 90 Q1110 45 1000 20 Z" fill="#10a89a"/>
  </svg>
  <div class="newsletter abs">
    <h2>Join Our Newsletter</h2>
    <p>Signup today for free and be the first to get notified on new updates.</p>
    <div class="email-field">Enter Email</div>
    <a class="btn" href="#"><span class="btn-icon"></span>Subscribe</a>
  </div>
  <div class="footer-brand abs"><div class="brand"><span class="brand-dot"></span><span>Restored<br>Together</span></div></div>
  <nav class="footer-nav abs">
    <a href="#">Home</a><a href="#">About Us</a><a href="#">Meetings &amp; Events</a><a href="#">Encounter</a><a href="#">Healing Rooms</a><a href="#">Live Stream</a>
  </nav>
  <div class="socials abs">
    <a href="#" aria-label="Share"><svg width="20" height="20" viewBox="0 0 20 20" fill="none" stroke="#fff" stroke-width="2"><circle cx="15" cy="4" r="2.5"/><circle cx="5" cy="10" r="2.5"/><circle cx="15" cy="16" r="2.5"/><path d="M7 9l6-4M7 11l6 4"/></svg></a>
    <a href="#" aria-label="Link"><svg width="20" height="20" viewBox="0 0 20 20" fill="none" stroke="#fff" stroke-width="2"><path d="M8 12l4-4"/><path d="M9 5l2-2a3.5 3.5 0 015 5l-2 2"/><path d="M11 15l-2 2a3.5 3.5 0 01-5-5l2-2"/></svg></a>
    <a href="#" aria-label="Email"><svg width="20" height="16" viewBox="0 0 20 16" fill="none" stroke="#fff" stroke-width="2"><rect x="1" y="1" width="18" height="14" rx="2"/><path d="M1 3l9 6 9-6"/></svg></a>
    <a href="#" aria-label="Heart"><svg width="20" height="18" viewBox="0 0 20 18" fill="none" stroke="#fff" stroke-width="2"><path d="M10 16S2 11 2 6a4 4 0 018-1 4 4 0 018 1c0 5-8 10-8 10z"/></svg></a>
    <a href="#" aria-label="Globe"><svg width="20" height="20" viewBox="0 0 20 20" fill="none" stroke="#fff" stroke-width="2"><circle cx="10" cy="10" r="8"/><path d="M2 10h16M10 2c3 3 3 13 0 16M10 2c-3 3-3 13 0 16"/></svg></a>
  </div>
  <p class="copyright abs">Copyrights 2025. Restored Together. All Rights Reserved</p>
</footer>

</body>
</html>
```